KLV Plant Services

We are a heavy diesel mechanical business with additional air con certificates, remapping engine rebuilt

Contact Information for Business Card

Company Name, Director Name, Managing Director, Contact details, email and website

Font styles to use
Serif
Script

```html
<!DOCTYPE html>
<html lang="en">
<head>
<meta charset="utf-8">
<title>KLV Plant Services – Business Card</title>
<link href="https://fonts.googleapis.com/css2?family=Noto+Serif:wght@400;700&display=swap" rel="stylesheet">
<style>
  :root {
    --stage: #3b3b3d;
    --navy: #2b2a7a;
    --navy-deep: #23226a;
    --ink: #111111;
    --paper: #ffffff;
    --text-grey: #333333;
  }
  html, body {
    margin: 0;
    padding: 0;
    width: 1200px;
    height: 780px;
    overflow: hidden;
    background: var(--stage);
  }
  .canvas {
    position: relative;
    width: 1200px;
    height: 780px;
    display: flex;
    align-items: center;
    justify-content: center;
    gap: 40px;
    font-family: "Noto Serif", Georgia, serif;
  }
  .card {
    position: relative;
    width: 540px;
    height: 309px;
    border-radius: 16px;
    overflow: hidden;
  }
  .card-front { background: var(--paper); }
  .card-back {
    background: var(--navy-deep);
    display: flex;
    align-items: center;
    justify-content: center;
  }
  .front-wave {
    position: absolute;
    inset: 0;
    width: 100%;
    height: 100%;
  }
  .brand {
    position: absolute;
    display: flex;
    align-items: center;
    gap: 12px;
    font-weight: 700;
    color: var(--navy);
  }
  .brand-front { left: 34px; top: 70px; }
  .brand-mark {
    width: 18px;
    height: 18px;
    border-radius: 50%;
    background: currentColor;
    flex: none;
  }
  .brand-name { line-height: 1.05; }
  .brand-name .brand-main { display: block; font-size: 46px; letter-spacing: 1px; }
  .brand-name .brand-sub { display: block; font-size: 17px; }
  .brand-back { position: static; color: var(--paper); gap: 18px; }
  .brand-back .brand-mark { width: 26px; height: 26px; }
  .brand-back .brand-main { font-size: 76px; }
  .brand-back .brand-sub { font-size: 28px; }
  .divider {
    position: absolute;
    left: 262px;
    top: 44px;
    width: 1px;
    height: 170px;
    background: var(--navy);
  }
  .contact {
    position: absolute;
    left: 282px;
    top: 46px;
    color: var(--navy);
  }
  .contact-name {
    margin: 0;
    font-size: 21px;
    font-weight: 700;
    letter-spacing: 0.5px;
    text-transform: uppercase;
  }
  .contact-role {
    margin: 2px 0 12px;
    font-size: 14px;
  }
  .contact-list {
    list-style: none;
    margin: 0;
    padding: 0;
    font-size: 14px;
    color: var(--text-grey);
  }
  .contact-list li {
    display: flex;
    align-items: center;
    gap: 7px;
    margin-bottom: 4px;
  }
  .contact-icon { width: 12px; height: 12px; flex: none; color: var(--navy); }
  .contact-address {
    margin: 6px 0 0;
    font-size: 14px;
    line-height: 1.35;
    color: var(--text-grey);
  }
</style>
</head>
<body>
<main class="canvas">

  <section class="card card-front" aria-label="Business card front">
    <svg class="front-wave" viewBox="0 0 540 309" preserveAspectRatio="none" aria-hidden="true">
      <path d="M0 200 C 120 190, 200 215, 290 250 S 450 300, 540 286 L540 309 L0 309 Z" fill="var(--ink)"/>
      <path d="M0 207 C 120 198, 200 223, 290 258 S 450 308, 540 294 L540 309 L0 309 Z" fill="var(--paper)"/>
      <path d="M0 213 C 120 205, 200 230, 290 265 S 450 312, 540 300 L540 309 L0 309 Z" fill="var(--navy)"/>
    </svg>

    <div class="brand brand-front">
      <span class="brand-mark" aria-hidden="true"></span>
      <span class="brand-name"><span class="brand-main">KLV</span><span class="brand-sub">Plant Services</span></span>
    </div>

    <div class="divider" aria-hidden="true"></div>

    <div class="contact">
      <h1 class="contact-name">Owen Harlow</h1>
      <p class="contact-role">Managing Director</p>
      <ul class="contact-list">
        <li>
          <svg class="contact-icon" viewBox="0 0 12 12" aria-hidden="true"><path d="M2.5 1 L4.5 1 L5.2 3.6 L4 4.5 C4.6 5.9 6 7.3 7.4 7.9 L8.4 6.8 L11 7.5 L11 9.5 C11 10.3 10.3 11 9.5 11 C5 11 1 7 1 2.5 C1 1.7 1.7 1 2.5 1 Z" fill="currentColor"/></svg>
          123 456 789
        </li>
        <li>
          <svg class="contact-icon" viewBox="0 0 12 12" aria-hidden="true"><rect x="0.5" y="2" width="11" height="8" rx="1" fill="currentColor"/><path d="M1 2.6 L6 6.6 L11 2.6" fill="none" stroke="#fff" stroke-width="1"/></svg>
          info@yourgmail.com
        </li>
        <li>
          <svg class="contact-icon" viewBox="0 0 12 12" aria-hidden="true"><circle cx="6" cy="6" r="5.2" fill="currentColor"/><path d="M1 6 H11 M6 0.8 C3.5 3.5 3.5 8.5 6 11.2 M6 0.8 C8.5 3.5 8.5 8.5 6 11.2" fill="none" stroke="#fff" stroke-width="0.8"/></svg>
          www.yourwebsite.com
        </li>
      </ul>
      <p class="contact-address">Your address, City<br>State, Zip 1234</p>
    </div>
  </section>

  <section class="card card-back" aria-label="Business card back">
    <div class="brand brand-back">
      <span class="brand-mark" aria-hidden="true"></span>
      <span class="brand-name"><span class="brand-main">KLV</span><span class="brand-sub">Plant Services</span></span>
    </div>
  </section>

</main>
</body>
</html>
```